Brintel Works - Fast, Efficient and Gas Mainteance for Domestic, Commercial and Industrial clients

We are in the process of purchasing a new business and would like to get a new logo and business card.
Business is a gas maintenance business that also does new gas installations.
Has been established since 1988.
Services include:
Install all types of gas appliances & equipment inc. hot water units
Maintain / repair / replace all types of gas appliances & equipment

Target Market(s)

Domestic, Commercial and Industrial clients

Industry/Entity Type

Business

Contact Information for Business Card

admin@brintelworks.com.au
07 3918 4726
Brintel Works PTY LTD

Logo Text

Gas Fitting & Plumbing Maintenance Specialists

Font styles to use
Sans Serif

Requirements
Must have
• Logo
• Business name, contact number, email address, web address
• Domestic | Commercial | Industrial Est Since 1988
Nice to have
• Possibly a black card with a flame logo to one side
Should not have
• Spelling errors

```html
<!DOCTYPE html>
<html lang="en">
<head>
<meta charset="utf-8">
<title>Brintel Works – Business Card</title>
<link href="https://fonts.googleapis.com/css2?family=Roboto:wght@400;500;700;900&display=swap" rel="stylesheet">
<style>
  :root {
    --backdrop: #ebebea;
    --card-black: #050505;
    --flame-red: #d70a05;
    --flame-orange: #f07d0c;
    --brand-orange: #ea5a12;
    --ink: #0b0b0b;
    --shadow: rgba(0, 0, 0, 0.18);
  }
  * { box-sizing: border-box; margin: 0; padding: 0; }
  html, body {
    width: 1200px; height: 857px; overflow: hidden;
    background: var(--backdrop);
    font-family: "Roboto", Arial, sans-serif;
  }
  .stage {
    position: relative; width: 1200px; height: 857px;
    display: flex; align-items: center; justify-content: center; gap: 56px;
  }
  .card {
    position: relative; width: 520px; height: 296px;
    border-radius: 34px; overflow: hidden;
    box-shadow: 0 10px 28px var(--shadow);
  }
  /* Front */
  .card--front {
    background: var(--card-black);
    display: flex; align-items: center; justify-content: center;
  }
  .brand { display: flex; align-items: center; gap: 14px; }
  .brand__dot {
    width: 44px; height: 44px; border-radius: 50%;
    background: var(--brand-orange); flex: none;
  }
  .brand__text { color: var(--brand-orange); }
  .brand__name {
    font-weight: 700; font-size: 40px; line-height: 1; letter-spacing: 0.5px;
    text-transform: uppercase;
  }
  .brand__entity {
    font-weight: 700; font-size: 15px; letter-spacing: 0.4px; margin-top: 4px;
  }
  /* Back */
  .card--back {
    background: linear-gradient(100deg, var(--flame-red) 0%, var(--flame-red) 35%, var(--flame-orange) 100%);
    display: flex; align-items: center; padding: 0 30px 0 70px; gap: 34px;
  }
  .emblem-area {
    width: 150px; height: 150px; border-radius: 50%;
    background: var(--ink); flex: none;
  }
  .details { color: var(--ink); }
  .details__name {
    font-weight: 900; font-size: 17px; line-height: 1.05; text-transform: uppercase;
  }
  .details__sectors {
    list-style: none; margin: 6px 0 10px;
    font-weight: 700; font-size: 12.5px; line-height: 1.3; text-transform: uppercase;
  }
  .details__sectors li::before { content: "•"; margin-right: 6px; }
  .contact { list-style: none; font-size: 12.5px; line-height: 1.55; }
  .contact li { display: flex; align-items: center; gap: 6px; }
  .contact svg { width: 11px; height: 11px; flex: none; }
</style>
</head>
<body>
<main class="stage">
  <section class="card card--back" aria-label="Business card back">
    <div class="emblem-area" role="img" aria-label="Company flame emblem area"></div>
    <div class="details">
      <p class="details__name">Brintel Works<br>PTY. LTD.</p>
      <ul class="details__sectors">
        <li>Domestic</li>
        <li>Commercial</li>
        <li>Industrial Est Since 1988</li>
      </ul>
      <ul class="contact">
        <li>
          <svg viewBox="0 0 12 12" aria-hidden="true"><circle cx="6" cy="6" r="5.5" fill="#0b0b0b"/><rect x="3" y="4" width="6" height="4" fill="none" stroke="#f07d0c" stroke-width="0.9"/><path d="M3 4 L6 6.3 L9 4" fill="none" stroke="#f07d0c" stroke-width="0.9"/></svg>
          admin@brintelworks.com.au
        </li>
        <li>
          <svg viewBox="0 0 12 12" aria-hidden="true"><circle cx="6" cy="6" r="5.5" fill="#0b0b0b"/><path d="M4 3.2 L5 3 L5.6 4.6 L4.9 5.2 Q5.6 6.6 6.8 7.1 L7.4 6.4 L9 7 L8.8 8 Q6.5 8.6 4.6 6.6 Q3.3 5 4 3.2Z" fill="#f07d0c"/></svg>
          <strong>07 3918 4726</strong>
        </li>
        <li>
          <svg viewBox="0 0 12 12" aria-hidden="true"><circle cx="6" cy="6" r="5.5" fill="#0b0b0b"/><circle cx="6" cy="6" r="3" fill="none" stroke="#f07d0c" stroke-width="0.8"/><path d="M3 6 H9 M6 3 Q4.4 6 6 9 M6 3 Q7.6 6 6 9" fill="none" stroke="#f07d0c" stroke-width="0.7"/></svg>
          brintelworks.com.au
        </li>
      </ul>
    </div>
  </section>

  <section class="card card--front" aria-label="Business card front">
    <div class="brand">
      <span class="brand__dot" aria-hidden="true"></span>
      <div class="brand__text">
        <p class="brand__name">Brintel Works</p>
        <p class="brand__entity">SERVICES PTY. LTD.</p>
      </div>
    </div>
  </section>
</main>
</body>
</html>
```